Modern design company business card design

We are a design oriented construction firm. The owner is an architect and licensed General Contractor and accomplished furniture designer. We do new home construction and large scale remodeling and office design. We would like a design for our new business cards that is clean and modern, but relatable. We like the bright green color of our logo mixed with different shades of grey. We're also open to reinterpreting the logo.

Target Market(s)

Potential design clients,
Construction clients

Industry/Entity Type

Architecture

Contact Information for Business Card

Tall Maple Design | Build Inc. (optional with logo, Inc. optional)Jeffrey MorganOwner (optional)317.555.0148 cell317.431.8056 officejmorgan@greensquareinc.comwww.greensquareinc.com

Font styles to use
Sans Serif
Other font styles liked:
• Avenir

Requirements
Nice to have
• I like designs that have some continuity between the front and back, i.e. similar layouts or graphic elements that wrap around the card. I tend to prefer horizontal over vertical, but that's not a have to. I also tend to prefer white or recycled paper.

```html
<!DOCTYPE html>
<html lang="en">
<head>
<meta charset="utf-8">
<title>Tall Maple Design | Build – Business Card</title>
<link rel="stylesheet" href="https://fonts.googleapis.com/css2?family=Nunito+Sans:wght@400;600&display=swap">
<style>
  :root {
    --stage: #e9e7e3;
    --kraft: #a99f93;
    --kraft-light: #b8aea2;
    --green-bright: #a6db5a;
    --green-mid: #58c24a;
    --green-deep: #2fa63f;
    --ink-light: #ffffff;
    --ink-soft: #f2efe9;
  }
  * { box-sizing: border-box; margin: 0; padding: 0; }
  html, body { width: 1200px; height: 913px; overflow: hidden; }
  body {
    background: var(--stage);
    font-family: "Nunito Sans", "Avenir", sans-serif;
    position: relative;
  }
  .card {
    position: absolute;
    width: 525px;
    height: 300px;
    border-radius: 18px;
    overflow: hidden;
    background: linear-gradient(160deg, var(--kraft-light), var(--kraft));
    box-shadow: 0 10px 28px rgba(0,0,0,0.18);
    color: var(--ink-light);
  }
  .card--front { left: 60px; top: 200px; }
  .card--back { left: 615px; top: 413px; }

  .brand-name {
    position: absolute;
    font-weight: 400;
    color: var(--ink-light);
    letter-spacing: 0.06em;
    text-transform: uppercase;
    line-height: 1.2;
    white-space: nowrap;
  }
  .brand-name__line { display: block; }

  /* Front */
  .card--front .brand-name { left: 32px; top: 92px; font-size: 19px; }
  .card--front .brand-name__line + .brand-name__line { font-size: 11px; letter-spacing: 0.12em; }
  .holder { position: absolute; right: 40px; top: 40px; text-align: right; }
  .holder__name { font-weight: 600; font-size: 17px; letter-spacing: 0.06em; text-transform: uppercase; }
  .holder__role { font-size: 10px; color: var(--ink-soft); }
  .corner-tab {
    position: absolute; right: 0; top: 30px; width: 26px; height: 20px;
    background: linear-gradient(135deg, var(--green-bright), var(--green-mid));
  }
  .rule { position: absolute; left: 0; right: 0; top: 170px; height: 1px; background: var(--green-mid); }
  .contact-band {
    position: absolute; left: 0; right: 0; top: 182px; bottom: 0;
    background: linear-gradient(180deg, var(--green-bright) 0%, var(--green-mid) 45%, var(--green-deep) 100%);
  }
  .contact-list { list-style: none; position: absolute; left: 32px; top: 18px; font-size: 12px; line-height: 1.5; }
  .contact-list li { display: flex; align-items: center; gap: 8px; }
  .contact-list svg { width: 10px; height: 10px; fill: none; stroke: var(--ink-soft); stroke-width: 1.4; }

  /* Back */
  .card--back .brand-name { left: 0; right: 0; top: 112px; text-align: center; font-size: 30px; }
  .card--back .brand-name__line + .brand-name__line { font-size: 15px; letter-spacing: 0.14em; }
</style>
</head>
<body>
  <section class="card card--front" aria-label="Card front">
    <p class="brand-name"><span class="brand-name__line">Tall Maple</span><span class="brand-name__line">Design | Build</span></p>
    <div class="corner-tab"></div>
    <div class="holder">
      <p class="holder__name">Dennis Holloway</p>
      <p class="holder__role">Owner</p>
    </div>
    <div class="rule"></div>
    <div class="contact-band">
      <ul class="contact-list">
        <li><svg viewBox="0 0 10 10"><rect x="2.5" y="1" width="5" height="8" rx="1"/></svg>317.555.0172</li>
        <li><svg viewBox="0 0 10 10"><path d="M2 1.5l2 2-1 1.2a6 6 0 0 0 2.3 2.3L6.5 6l2 2-1.2 1.2C4 9 1 6 .8 2.7z"/></svg>317.555.0148</li>
        <li><svg viewBox="0 0 10 10"><circle cx="5" cy="5" r="4"/><path d="M1 5h8M5 1c-2 2.5-2 5.5 0 8M5 1c2 2.5 2 5.5 0 8"/></svg>www.tallmapleinc.example</li>
        <li><svg viewBox="0 0 10 10"><rect x="1" y="2.2" width="8" height="5.6"/><path d="M1 2.2l4 3.3 4-3.3"/></svg>dholloway@tallmapleinc.example</li>
      </ul>
    </div>
  </section>

  <section class="card card--back" aria-label="Card back">
    <p class="brand-name"><span class="brand-name__line">Tall Maple</span><span class="brand-name__line">Design | Build</span></p>
  </section>
</body>
</html>
```